Investment Advisor E-Newsletter Banner Design

I need a banner designed for an email newsletter that will be sent monthly to clients and prospects. We want to see designs that are elegant and use our logo well. The banner should be 922x150px and should go well with the www.tlvbanda.com website. Should include Logo and email and phone number.

Target Market(s)

High net worth investors

Number of Pages Required

1 page

Requirements
Must have
• logo, place for email (info@tlvbanda.com) and phone number (415-297-6180), colors and design that work well with www.tlvbanda.com website

```html
<!DOCTYPE html>
<html lang="en">
<head>
<meta charset="utf-8">
<title>Tall Vale Banda – Newsletter Banner</title>
<link rel="stylesheet" href="https://fonts.googleapis.com/css2?family=Cormorant+Garamond:ital,wght@0,500;1,500&display=swap">
<style>
  :root {
    --denim-light: #4a5f80;
    --denim-mid: #3a4e6e;
    --denim-dark: #2b3b57;
    --panel-black: #0c0c0c;
    --icon-blue: #0d1c9e;
    --text-white: #ffffff;
    --photo-light: #eef0f2;
    --photo-mid: #c9ccd0;
    --photo-dark: #6b6e74;
  }
  * { margin: 0; padding: 0; box-sizing: border-box; }
  html, body {
    width: 1200px;
    height: 195px;
    overflow: hidden;
    background: #ffffff;
  }
  .banner {
    position: relative;
    width: 1200px;
    height: 195px;
    overflow: hidden;
    font-family: "Cormorant Garamond", Georgia, serif;
    color: var(--text-white);
  }
  .denim-field {
    position: absolute;
    inset: 0 600px 0 0;
    background: radial-gradient(ellipse at 35% 45%, var(--denim-light), var(--denim-mid) 55%, var(--denim-dark));
  }
  .advisor-photo {
    position: absolute;
    top: 0;
    right: 0;
    width: 380px;
    height: 195px;
    background: linear-gradient(100deg, var(--photo-mid) 0%, var(--photo-light) 35%, var(--photo-dark) 60%, var(--photo-light) 85%, var(--photo-mid) 100%);
  }
  .wave-shapes {
    position: absolute;
    inset: 0;
  }
  .brand {
    position: absolute;
    left: 48px;
    top: 34px;
    display: flex;
    align-items: center;
    gap: 26px;
  }
  .brand-mark {
    width: 62px;
    height: 62px;
    background: var(--text-white);
    flex: none;
  }
  .brand-name {
    font-weight: 500;
    font-style: normal;
    line-height: 1.1;
    white-space: nowrap;
  }
  .brand-name .primary { display: block; font-size: 46px; }
  .brand-name .secondary { display: block; font-size: 22px; margin-top: 4px; }
  .contact-list {
    position: absolute;
    left: 598px;
    top: 38px;
    list-style: none;
  }
  .contact-item {
    display: flex;
    align-items: center;
    height: 46px;
    margin-bottom: 30px;
  }
  .contact-icon {
    width: 46px;
    height: 46px;
    flex: none;
  }
  .contact-text {
    margin-left: 18px;
    font-size: 21px;
    font-style: italic;
    font-weight: 500;
    letter-spacing: 0.2px;
  }
</style>
</head>
<body>
<div class="banner">
  <div class="denim-field"></div>
  <div class="advisor-photo" role="img" aria-label="Photo of two smiling advisors in business attire reviewing documents at a bright office desk"></div>

  <svg class="wave-shapes" width="1200" height="195" viewBox="0 0 1200 195" aria-hidden="true">
    <path d="M515,0 C565,50 482,140 545,195 L900,195 C848,150 842,58 895,0 Z" fill="var(--panel-black)"/>
  </svg>

  <div class="brand">
    <div class="brand-mark"></div>
    <div class="brand-name">
      <span class="primary">Tall Vale Banda</span>
      <span class="secondary">Management &amp; Research, Inc.</span>
    </div>
  </div>

  <ul class="contact-list">
    <li class="contact-item">
      <svg class="contact-icon" viewBox="0 0 46 46" aria-hidden="true">
        <circle cx="23" cy="23" r="23" fill="var(--icon-blue)"/>
        <rect x="13" y="16" width="20" height="14" fill="var(--text-white)"/>
        <path d="M13,16 L23,24 L33,16" fill="none" stroke="var(--icon-blue)" stroke-width="1.6"/>
      </svg>
      <span class="contact-text">info@tlvbanda.com</span>
    </li>
    <li class="contact-item">
      <svg class="contact-icon" viewBox="0 0 46 46" aria-hidden="true">
        <circle cx="23" cy="23" r="23" fill="var(--icon-blue)"/>
        <path d="M16.5,13 l4,0 l1.8,5.5 l-2.6,2 c1.2,2.6 3.2,4.6 5.8,5.8 l2,-2.6 l5.5,1.8 l0,4 c0,1.2 -1,2 -2.2,2 c-8.5,-0.6 -15.3,-7.4 -15.9,-15.9 c0,-1.2 0.8,-2.6 1.6,-2.6 Z" fill="var(--text-white)"/>
      </svg>
      <span class="contact-text">415-297-6180</span>
    </li>
  </ul>
</div>
</body>
</html>
```